High Tech Real Estate Startup needs a business card

We are developing an innovative real estate marketing product based around advanced search and virtual reality.

We talk to people, we need business cards.

Target Market(s)

The target market is technology professionals and realtors.

Contact Information for Business Card

The information to be included will include

Name
Title
Phone Number
E-mail Address
www.zelquin.com

It should use simple iconography for each one of those fields.

Font styles to use
Other font styles liked:
• Co, Jubilat, Avenir

Colors

Designer to choose colors to be used in the design.

Requirements
Must have
• Clean aesthetic,
• Good use of negative space.
• It should use our company logo, shown in the attached file. It is able to use the negative of that logo (coloured font and white background) and I have attached other acceptable accent colours in a swatch file.
Should not have
• Should not be too busy
• No extraneous text (slogans, tag lines etc)

```html
<!DOCTYPE html>
<html lang="en">
<head>
<meta charset="utf-8">
<title>Zelquin Business Card</title>
<link rel="stylesheet" href="https://fonts.googleapis.com/css2?family=Open+Sans:wght@400;600&display=swap">
<style>
  :root {
    --backdrop: #3b3b3d;
    --card: #232325;
    --teal: #3fb6b8;
    --ink-light: #f2f2f2;
    --ink-muted: #6b6b6d;
  }
  * { margin: 0; padding: 0; box-sizing: border-box; }
  html, body { width: 799px; height: 1200px; overflow: hidden; }
  body {
    background: var(--backdrop);
    font-family: "Open Sans", Arial, sans-serif;
    position: relative;
  }
  .card {
    position: absolute;
    left: 100px;
    width: 600px;
    height: 343px;
    background: var(--card);
    border-radius: 26px;
    overflow: hidden;
  }
  .card-front { top: 130px; }
  .card-back { top: 727px; }
  .brand-name {
    position: absolute;
    color: var(--teal);
    font-weight: 400;
    letter-spacing: 4px;
    line-height: 1;
    white-space: nowrap;
  }
  .card-front .brand-name {
    font-size: 64px;
    left: 0; right: 0; top: 138px;
    text-align: center;
  }
  .accent-band {
    position: absolute;
    left: 0; top: 0; bottom: 0;
    width: 62px;
    background: var(--teal);
  }
  .card-back .brand-name {
    font-size: 56px;
    left: 112px; top: 48px;
  }
  .holder { position: absolute; left: 112px; top: 168px; }
  .holder-name { color: var(--teal); font-size: 22px; font-weight: 600; line-height: 1.1; white-space: nowrap; }
  .holder-title { color: var(--ink-muted); font-size: 13px; font-weight: 600; margin-top: 2px; white-space: nowrap; }
  .contact-list { position: absolute; left: 112px; top: 240px; list-style: none; }
  .contact-item {
    display: flex; align-items: center; gap: 10px;
    color: var(--ink-light); font-size: 15px; font-weight: 600;
    height: 24px;
    white-space: nowrap;
  }
  .contact-icon { width: 16px; height: 16px; flex: none; }
</style>
</head>
<body>
  <section class="card card-front">
    <div class="brand-name">ZELQUIN</div>
  </section>

  <section class="card card-back">
    <div class="accent-band"></div>
    <div class="brand-name">ZELQUIN</div>
    <div class="holder">
      <div class="holder-name">Alan Reyes Clark</div>
      <div class="holder-title">Managing Director</div>
    </div>
    <ul class="contact-list">
      <li class="contact-item">
        <svg class="contact-icon" viewBox="0 0 16 16"><circle cx="8" cy="8" r="8" fill="#3fb6b8"/><path d="M5.2 4.2l1.4-.4.9 2-1 .8a5 5 0 002.9 2.9l.8-1 2 .9-.4 1.4c-3.6.3-6.9-3-6.6-6.6z" fill="#232325"/></svg>
        312.840.2719
      </li>
      <li class="contact-item">
        <svg class="contact-icon" viewBox="0 0 16 16"><circle cx="8" cy="8" r="8" fill="#3fb6b8"/><rect x="4" y="5.2" width="8" height="5.6" fill="#232325"/><path d="M4 5.2l4 3 4-3" fill="none" stroke="#3fb6b8" stroke-width=".9"/></svg>
        alan@zelquin.com
      </li>
      <li class="contact-item">
        <svg class="contact-icon" viewBox="0 0 16 16"><circle cx="8" cy="8" r="8" fill="#3fb6b8"/><circle cx="8" cy="8" r="4" fill="none" stroke="#232325" stroke-width="1"/><path d="M4 8h8M8 4c-1.6 2.4-1.6 5.6 0 8M8 4c1.6 2.4 1.6 5.6 0 8" fill="none" stroke="#232325" stroke-width=".9"/></svg>
        www.zelquin.com
      </li>
    </ul>
  </section>
</body>
</html>
```